We need a web page design for a new company called "Brambel". We provide an innovative music sharing mobile application that allows music listeners to share their music without paying for a monthly subscription. We would like to incorporate the attached logo and color scheme. The final design should communicate music gifting and sharing.

Industry/Entity Type

It Company

```html
<!DOCTYPE html>
<html lang="en">
<head>
<meta charset="utf-8">
<title>Brambel — share the music</title>
<link rel="stylesheet" href="https://fonts.googleapis.com/css2?family=Roboto:ital,wght@0,400;0,500;0,700;1,700&family=Lato:wght@400;700&display=swap">
<style>
:root{
  --green:#62a70f;
  --green-dark:#5b9c0c;
  --green-light:#8dc152;
  --orange:#f7931e;
  --orange-dark:#f08a12;
  --text:#333333;
  --muted:#777777;
  --grey-btn:#9a9a9a;
  --cream:#ece8d9;
  --footer:#333333;
  --footer-base:#272727;
  --white:#ffffff;
}
*{box-sizing:border-box;margin:0;padding:0}
html,body{width:821px;height:1200px;overflow:hidden;background:var(--white)}
body{position:relative;font-family:"Roboto",Arial,sans-serif;color:var(--text)}

/* header */
.site-header{position:absolute;left:0;top:0;width:821px;height:60px;background:var(--green)}
.brand-name{position:absolute;left:122px;top:14px;font-family:"Lato",sans-serif;font-weight:700;font-size:28px;line-height:30px;color:var(--white)}
.nav{position:absolute;left:379px;top:0;display:flex;height:60px}
.nav a{display:block;height:60px;line-height:78px;font-size:9px;font-weight:700;color:var(--white);text-decoration:none;padding:0 9px}
.nav a + a{padding-left:18px}
.nav a.active{background:var(--white);color:var(--text)}
.account{position:absolute;left:680px;top:13px;font-size:8px;color:var(--white);letter-spacing:.3px}

/* hero */
.hero{position:absolute;left:0;top:60px;width:821px;height:263px;background:linear-gradient(100deg,#d9d3c8 0%,#e9e6e1 30%,#c9d9e6 55%,#7b94b0 85%,#5d7a98 100%)}

/* features */
.features{position:absolute;left:113px;top:323px;width:640px;height:130px;display:flex}
.feature{position:relative;width:160px;height:130px;text-align:center;color:var(--white)}
.feature:nth-child(odd){background:var(--green)}
.feature:nth-child(even){background:var(--green-light)}
.feature-icon{position:absolute;left:39px;top:-42px;width:82px;height:82px;border-radius:50%;background:var(--white);border:3px solid var(--green);display:flex;align-items:center;justify-content:center}
.feature h3{position:absolute;left:0;right:0;top:52px;font-size:12px;font-weight:500}
.feature p{position:absolute;left:14px;right:14px;top:70px;font-size:9px;line-height:11px;color:#eef6e4}
.feature-plus{position:absolute;left:69px;top:111px;width:21px;height:19px;background:var(--orange);border:2px solid var(--white);border-bottom:0}
.feature-plus::before,.feature-plus::after{content:"";position:absolute;background:var(--white)}
.feature-plus::before{left:4px;top:7px;width:9px;height:2px}
.feature-plus::after{left:7.5px;top:3px;width:2px;height:10px}

/* section titles */
.section-title{position:absolute;left:113px;padding-left:4px;border-left:2px solid var(--green);font-size:14px;font-weight:400;line-height:15px;color:var(--text)}
.slider-arrows{position:absolute;left:718px;top:482px;display:flex;gap:2px}
.slider-arrows span{width:16px;height:16px;background:#c8c8c8}
.slider-arrows span:last-child{background:var(--green)}

/* tracks */
.track{position:absolute;top:510px;width:147px;height:192px;border-bottom:2px solid var(--green)}
.track-cover{position:relative;width:147px;height:146px;border:5px solid var(--green)}
.track-cover.featured{border-color:var(--orange)}
.track-art{width:100%;height:100%}
.track-title{font-size:8.6px;font-weight:700;font-style:italic;margin-top:7px;white-space:nowrap}
.track-actions{display:flex;justify-content:space-between;margin-top:5px}
.btn-share,.btn-gift{width:40px;height:15px;font-size:8px;font-weight:500;color:var(--white);display:flex;align-items:center;justify-content:center}
.btn-share{background:var(--green)}
.btn-gift{background:var(--grey-btn)}
.play{position:absolute;left:45px;top:45px;width:46px;height:46px;border-radius:50%;background:rgba(90,90,90,.75)}

/* call to action */
.cta{position:absolute;left:113px;top:726px;width:640px;height:59px;background:var(--cream);border:1px solid #d9d4c0}
.cta p{position:absolute;left:6px;top:20px;font-size:14px;color:var(--text);white-space:nowrap}
.cta-btn{position:absolute;left:543px;top:14px;width:87px;height:28px;background:var(--green);color:var(--white);font-size:9.5px;font-weight:700;display:flex;align-items:center;justify-content:center}

/* categories */
.read-more{position:absolute;left:684px;top:815px;width:67px;height:19px;background:var(--orange-dark);color:var(--text);font-size:8px;font-weight:700;display:flex;align-items:center;justify-content:center}
.cat-divider{position:absolute;left:113px;top:845px;width:640px;height:1px;background:#eeeeee}
.cat-col{position:absolute;top:856px;width:81px;list-style:none}
.cat-item{position:relative;height:26.6px;border-bottom:1px solid #eeeeee;font-size:9px;line-height:18px;padding-left:16px;color:var(--text)}
.cat-item::before{content:"";position:absolute;left:0;top:4px;width:10px;height:10px;border-radius:50%;background:#c9c9c9}
.cat-item::after{content:"";position:absolute;right:0;top:5px;width:8px;height:8px;background:var(--green)}
.cat-item.active{color:var(--green)}

/* footer */
.footer{position:absolute;left:0;top:1038px;width:821px;height:134px;background:var(--footer);border-top:3px solid var(--green);color:#e6e6e6}
.footer h4{position:absolute;top:9px;font-family:"Lato",sans-serif;font-weight:400;font-size:13px;color:var(--white)}
.quick-links{position:absolute;left:116px;top:35px;list-style:none;font-size:8.5px;line-height:14.4px}
.quick-links li::before{content:"›";margin-right:6px}
.news-arrows{position:absolute;left:362px;top:13px;display:flex;gap:1px}
.news-arrows span{width:11px;height:11px;background:var(--green)}
.news-item{position:absolute;left:229px;width:170px;display:flex;gap:8px}
.news-date{width:26px;text-align:center;font-size:6px;font-weight:700}
.news-date b{display:block;background:var(--green);color:var(--white);font-size:9px;line-height:13px}
.news-date span{display:block;background:#eeeeee;color:var(--text);line-height:10px}
.news-text{font-size:8px;line-height:10px}
.news-text strong{color:var(--white)}
.newsletter p{position:absolute;left:430px;top:34px;width:140px;font-size:7.5px;line-height:12px}
.email-field{position:absolute;left:430px;top:67px;width:143px;height:18px;background:var(--white);color:#999;font-size:7px;font-style:italic;padding:5px 4px}
.subscribe{position:absolute;left:430px;top:93px;width:72px;height:20px;background:var(--green);color:var(--white);font-size:9.5px;font-weight:700;display:flex;align-items:center;justify-content:center}
.footer-divider{position:absolute;left:605px;top:22px;width:1px;height:95px;background:#444}
.footer-brand{position:absolute;left:622px;top:38px;width:130px;text-align:center;font-family:"Lato",sans-serif;font-weight:700;font-size:25px;line-height:28px;color:var(--white)}
.social{position:absolute;left:642px;top:93px;display:flex;gap:7px}
.social span{width:16px;height:16px;border-radius:50%;background:#555}
.social span.on{background:var(--green)}
.copyright{position:absolute;left:0;top:1172px;width:821px;height:28px;background:var(--footer-base);color:#dddddd;font-size:8px;text-align:center;line-height:30px}
.copyright b{color:var(--white)}
</style>
</head>
<body>

<header class="site-header">
  <div class="brand-name">Brambel</div>
  <nav class="nav">
    <a class="active">HOME</a><a>SERVICES</a><a>TIMETABLE</a><a>NEWS</a><a>FEATURES</a><a>CONTACTS</a>
  </nav>
  <div class="account">LOGIN &nbsp;|&nbsp; SIGNUP</div>
</header>

<div class="hero" role="img" aria-label="Photo of a man relaxing on a sofa wearing headphones and holding a phone"></div>

<section class="features">
  <div class="feature">
    <div class="feature-icon"><svg width="34" height="36" viewBox="0 0 34 36"><path d="M10 6 L32 1 V26" fill="none" stroke="#f7931e" stroke-width="4"/><path d="M10 6 V31" stroke="#f7931e" stroke-width="4"/><ellipse cx="6" cy="31" rx="6" ry="4.5" fill="#f7931e"/><ellipse cx="28" cy="26" rx="6" ry="4.5" fill="#f7931e"/></svg></div>
    <h3>UPLOAD MUSIC &amp; AUDIO</h3>
    <p>Lorem Ipsum is simply dummy text of the printing.</p>
    <span class="feature-plus"></span>
  </div>
  <div class="feature">
    <div class="feature-icon"><svg width="38" height="36" viewBox="0 0 38 36"><path d="M5 22 V18 A14 14 0 0 1 33 18 V22" fill="none" stroke="#f7931e" stroke-width="4"/><rect x="2" y="20" width="10" height="15" rx="3" fill="#f7931e"/><rect x="26" y="20" width="10" height="15" rx="3" fill="#f7931e"/></svg></div>
    <h3>LISTEN &amp; DISCOVER</h3>
    <p>Lorem Ipsum is simply dummy text of the printing fdsjoid.</p>
    <span class="feature-plus"></span>
  </div>
  <div class="feature">
    <div class="feature-icon"><svg width="40" height="34" viewBox="0 0 40 34"><circle cx="15" cy="9" r="8" fill="#f7931e"/><path d="M0 32 C0 20 30 20 30 32Z" fill="#f7931e"/><circle cx="28" cy="16" r="6" fill="#f7931e" stroke="#fff" stroke-width="2"/><path d="M18 34 C18 24 40 24 40 34Z" fill="#f7931e" stroke="#fff" stroke-width="2"/></svg></div>
    <h3>CONNECT</h3>
    <p>Lorem Ipsum is simply dummy text of the printing.</p>
    <span class="feature-plus"></span>
  </div>
  <div class="feature">
    <div class="feature-icon"><svg width="38" height="38" viewBox="0 0 38 38"><g stroke="#f7931e" stroke-width="3"><line x1="19" y1="19" x2="7" y2="7"/><line x1="19" y1="19" x2="32" y2="9"/><line x1="19" y1="19" x2="10" y2="32"/><line x1="19" y1="19" x2="31" y2="30"/></g><g fill="#f7931e"><circle cx="19" cy="19" r="6"/><circle cx="7" cy="7" r="5"/><circle cx="32" cy="9" r="4"/><circle cx="10" cy="32" r="4"/><circle cx="31" cy="30" r="5"/></g></svg></div>
    <h3>SHARE</h3>
    <p>Lorem Ipsum is simply dummy text of the printing fdsjoid.</p>
    <span class="feature-plus"></span>
  </div>
</section>

<h2 class="section-title" style="top:483px">TRENDING MUSIC &amp; AUDIO</h2>
<div class="slider-arrows"><span></span><span></span></div>

<article class="track" style="left:113px">
  <div class="track-cover"><div class="track-art" role="img" aria-label="Album cover artwork" style="background:linear-gradient(160deg,#9a9a9a,#3a3a3a 60%,#1c1c1c)"></div></div>
  <p class="track-title">Lorem ipsum dolor sfgjit rem Ipsumis</p>
  <div class="track-actions"><span class="btn-share">SHARE</span><span class="btn-gift">GIFT</span></div>
</article>
<article class="track" style="left:277px">
  <div class="track-cover featured"><div class="track-art" role="img" aria-label="Album cover artwork" style="background:radial-gradient(circle at 50% 50%,#b05a3a,#4a1e12 45%,#0d0d0d 70%)"></div><span class="play"></span></div>
  <p class="track-title">Lorem ipsum dolor sfgjit rem Ipsumis</p>
  <div class="track-actions"><span class="btn-share">SHARE</span><span class="btn-gift">GIFT</span></div>
</article>
<article class="track" style="left:440px">
  <div class="track-cover"><div class="track-art" role="img" aria-label="Album cover artwork" style="background:linear-gradient(135deg,#e0299a,#f3f3f3 55%,#e0299a)"></div></div>
  <p class="track-title">Lorem ipsum dolor sfgjit rem Ipsumis</p>
  <div class="track-actions"><span class="btn-share">SHARE</span><span class="btn-gift">GIFT</span></div>
</article>
<article class="track" style="left:604px">
  <div class="track-cover"><div class="track-art" role="img" aria-label="Album cover artwork" style="background:radial-gradient(circle at 50% 40%,#c9a154,#6b4a1e 55%,#2a1c0c)"></div></div>
  <p class="track-title">Lorem ipsum dolor sfgjit rem Ipsumis</p>
  <div class="track-actions"><span class="btn-share">SHARE</span><span class="btn-gift">GIFT</span></div>
</article>

<section class="cta">
  <p>So are you ready to discover new music and sounds and share them with the world?</p>
  <span class="cta-btn">SIGN UP NOW</span>
</section>

<h2 class="section-title" style="top:817px">MUSIC CATEGORIES</h2>
<span class="read-more">READ MORE</span>
<div class="cat-divider"></div>

<ul class="cat-col" style="left:113px">
  <li class="cat-item active">Acoustic</li><li class="cat-item">Music-Pack</li><li class="cat-item">Drum’n’ Bass</li><li class="cat-item">Alternative</li><li class="cat-item">Eurodance</li><li class="cat-item">Ambient</li>
</ul>
<ul class="cat-col" style="left:220px">
  <li class="cat-item">Acoustic</li><li class="cat-item">Music-Pack</li><li class="cat-item">Drum’n’ Bass</li><li class="cat-item">Alternative</li><li class="cat-item">Eurodance</li><li class="cat-item">Ambient</li>
</ul>
<ul class="cat-col" style="left:329px">
  <li class="cat-item">Acoustic</li><li class="cat-item">Music-Pack</li><li class="cat-item">Drum’n’ Bass</li><li class="cat-item">Alternative</li><li class="cat-item">Eurodance</li><li class="cat-item">Ambient</li>
</ul>
<ul class="cat-col" style="left:439px">
  <li class="cat-item">Acoustic</li><li class="cat-item">Music-Pack</li><li class="cat-item">Drum’n’ Bass</li><li class="cat-item">Alternative</li><li class="cat-item">Eurodance</li><li class="cat-item">Ambient</li>
</ul>
<ul class="cat-col" style="left:551px">
  <li class="cat-item">Acoustic</li><li class="cat-item">Music-Pack</li><li class="cat-item">Drum’n’ Bass</li><li class="cat-item">Alternative</li><li class="cat-item">Eurodance</li><li class="cat-item">Ambient</li>
</ul>
<ul class="cat-col" style="left:668px;width:84px">
  <li class="cat-item">Acoustic</li><li class="cat-item">Music-Pack</li><li class="cat-item">Drum’n’ Bass</li><li class="cat-item">Alternative</li><li class="cat-item">Eurodance</li><li class="cat-item">Ambient</li>
</ul>

<footer class="footer">
  <h4 style="left:113px">Quick Links</h4>
  <ul class="quick-links"><li>Home</li><li>Services</li><li>Timetable</li><li>News</li><li>Features</li><li>Contact Us</li></ul>

  <h4 style="left:229px">News Updates</h4>
  <div class="news-arrows"><span></span><span></span></div>
  <div class="news-item" style="top:40px">
    <div class="news-date"><b>12</b><span>NOV</span></div>
    <div class="news-text"><strong>Vero eros accumsaet odio</strong><br>quis nostrud exetiperj suscipit<br>nisl ut aliquip ex ea commod</div>
  </div>
  <div class="news-item" style="top:86px">
    <div class="news-date"><b>20</b><span>NOV</span></div>
    <div class="news-text"><strong>Vero eros accumsaet odio</strong><br>quis nostrud exetiperj suscipit<br>nisl ut aliquip ex ea commod</div>
  </div>

  <div class="newsletter">
    <h4 style="left:430px">Newsletter Sign Up</h4>
    <p>Lorem ipsudolor sit coec adipiscing elitsite amet</p>
    <div class="email-field">Email Address</div>
    <span class="subscribe">SUBSCRIBE</span>
  </div>

  <div class="footer-divider"></div>
  <div class="footer-brand">Brambel</div>
  <div class="social"><span></span><span class="on"></span><span></span><span></span></div>
</footer>

<div class="copyright">© 2014 <b>BrambelMusic</b>. All Rights Reserved.</div>

</body>
</html>
```